Acupuncture business needs business card design

I need a business card for an acupuncture clinic called "Harbourlight Wellness"
It will need the following details:
My name: Marcus Pelling
Acupuncturist
Member TVBH
KWF Treatment Provider
Ph numbers: 581 2734 027 418 5620
Email: marcus@hbwel.example.nz
On the back it will need a table with 2 columns for appointments, one column for time and one for date.

Industry/Entity Type

Clinic

Contact Information for Business Card

Marcus Pelling
Acupuncturist
Member TVBH
KWF Treatment Provider
Email: marcus@hbwel.example.nz

Requirements
Must have
• Marcus Pelling
• Acupuncturist
• Member TVBH
• KWF Treatment Provider
• Ph numbers: 581 2734 027 418 5620
• Email: marcus@hbwel.example.nz
• On the back it will need a table with 2 columns for appointments, one column for time and one for date.

```html
<!DOCTYPE html>
<html lang="en">
<head>
<meta charset="utf-8">
<title>Harbourlight Wellness – Business Card</title>
<link rel="stylesheet" href="https://fonts.googleapis.com/css2?family=Source+Sans+3:wght@400;600;700&display=swap">
<style>
  :root {
    --brand-blue: #13a9dc;
    --brand-blue-dark: #0f8fbf;
    --ink: #2b2f33;
    --ink-soft: #4a5258;
    --paper: #ffffff;
    --backdrop: #e9ecee;
    --slot: rgba(255, 255, 255, 0.72);
    --faint-mark: #dcebf1;
  }
  * { box-sizing: border-box; margin: 0; padding: 0; }
  html, body { width: 1200px; height: 948px; overflow: hidden; }
  body {
    background: var(--backdrop);
    font-family: "Source Sans 3", Arial, sans-serif;
    display: flex;
    flex-direction: column;
    align-items: center;
    justify-content: center;
    gap: 40px;
  }
  .card {
    position: relative;
    width: 760px;
    height: 434px;
    overflow: hidden;
    box-shadow: 0 4px 14px rgba(0,0,0,0.12);
  }

  /* Front */
  .card--front { background: var(--paper); }
  .front-band {
    position: absolute; left: 0; top: 0; width: 100%; height: 62px;
  }
  .brand {
    position: absolute; left: 28px; top: 14px;
    display: flex; align-items: center; gap: 18px;
  }
  .brand-dot {
    width: 70px; height: 70px; border-radius: 50%;
    background: var(--brand-blue-dark);
    border: 6px solid var(--paper);
  }
  .brand-name {
    position: absolute; left: 124px; top: 72px;
    font-size: 52px; font-weight: 600; color: var(--brand-blue);
    letter-spacing: -0.5px; line-height: 1;
  }
  .brand-tagline {
    position: absolute; left: 128px; top: 132px;
    font-size: 17px; font-weight: 400; color: var(--brand-blue);
    letter-spacing: 6px; text-transform: uppercase;
  }
  .contact {
    position: absolute; left: 40px; top: 180px;
    color: var(--ink);
  }
  .contact-name {
    font-size: 22px; font-weight: 700; color: var(--ink-soft);
    margin-bottom: 4px;
  }
  .contact-role {
    font-size: 17px; color: var(--brand-blue); line-height: 1.3;
  }
  .contact-lines { margin-top: 18px; list-style: none; }
  .contact-lines li {
    display: flex; align-items: center; gap: 10px;
    font-size: 19px; line-height: 1.6; color: var(--ink);
  }
  .contact-icon { width: 18px; height: 18px; flex: none; }
  .front-mark {
    position: absolute; right: 70px; bottom: 40px;
    width: 200px; height: 200px; border-radius: 50%;
    background: var(--faint-mark);
  }

  /* Back */
  .card--back { background: var(--brand-blue); color: var(--paper); }
  .back-mark {
    position: absolute; left: 200px; top: 40px;
    width: 340px; height: 340px; border-radius: 50%;
    background: rgba(255,255,255,0.12);
  }
  .appointments {
    position: absolute; left: 60px; top: 50px;
    border-collapse: separate; border-spacing: 22px 16px;
  }
  .appointments th {
    text-align: left; font-weight: 400; font-size: 22px;
    letter-spacing: 1px; padding-left: 2px;
  }
  .slot {
    width: 270px; height: 38px; background: var(--slot);
  }
  .web-address {
    position: absolute; left: 82px; bottom: 46px;
    font-size: 24px; letter-spacing: 5px;
  }
</style>
</head>
<body>

  <section class="card card--front" aria-label="Business card front">
    <svg class="front-band" viewBox="0 0 760 62" preserveAspectRatio="none" aria-hidden="true">
      <polygon points="120,0 760,0 760,62 150,62" fill="var(--brand-blue)"/>
    </svg>
    <div class="brand"><span class="brand-dot"></span></div>
    <div class="brand-name">Harbourlight Wellness</div>
    <div class="brand-tagline">Acupuncture Physiotherapy</div>

    <div class="contact">
      <p class="contact-name">Marcus Pelling</p>
      <p class="contact-role">Acupuncturist · Member TVBH</p>
      <p class="contact-role">KWF Treatment Provider</p>
      <ul class="contact-lines">
        <li>
          <svg class="contact-icon" viewBox="0 0 24 24" aria-hidden="true"><circle cx="12" cy="12" r="12" fill="var(--brand-blue)"/><path d="M8 6l2 0 1 3-1.5 1a7 7 0 0 0 4 4l1-1.5 3 1 0 2a2 2 0 0 1-2 2A10 10 0 0 1 6 8a2 2 0 0 1 2-2z" fill="#fff"/></svg>
          581 2734 · 027 418 5620
        </li>
        <li>
          <svg class="contact-icon" viewBox="0 0 24 24" aria-hidden="true"><circle cx="12" cy="12" r="12" fill="var(--brand-blue)"/><rect x="6" y="8" width="12" height="8" fill="#fff"/><path d="M6 8l6 5 6-5" fill="none" stroke="var(--brand-blue)" stroke-width="1.2"/></svg>
          marcus@hbwel.example.nz
        </li>
      </ul>
    </div>
    <div class="front-mark" role="img" aria-label="Faint brand circle"></div>
  </section>

  <section class="card card--back" aria-label="Business card back">
    <div class="back-mark" role="img" aria-label="Faint brand circle"></div>
    <table class="appointments">
      <thead>
        <tr><th>Date</th><th>Time</th></tr>
      </thead>
      <tbody>
        <tr><td><div class="slot"></div></td><td><div class="slot"></div></td></tr>
        <tr><td><div class="slot"></div></td><td><div class="slot"></div></td></tr>
        <tr><td><div class="slot"></div></td><td><div class="slot"></div></td></tr>
      </tbody>
    </table>
    <p class="web-address">www.hbwel.example.nz</p>
  </section>

</body>
</html>
```